Luxury Business Card Design for High-End Window Treatments

Gilded Slatworks
Custom Plantation Shutters & Architectural Shading Systems

⸻

BACK

Daniel Trevick
Owner

Custom Interior & Exterior Window Treatments

919-555-0148
gildedslatworks.com

I have included a picture that I’m hoping we can use on the back, but I’m also wondering if you can get rid of the ladder? Should we get rid of shutters , shades and blinds underneath Gilded Slatworks?

Target Market(s)

High-end residential homeowners, custom home builders, architects, interior designers, and luxury renovation clients seeking premium plantation shutters and motorized architectural shading systems.

Industry/Entity Type

Custom Window treatments

Contact Information for Business Card

Front Gilded Slatworks Custom Plantation Shutters Motorized Architectural Shading Systems BACK Daniel Trevick Owner 919-555-0148 GildedSlatworks.com Custom Interior & Exterior Window Treatments By Appointment

Requirements
Nice to have
• Not 100% sure on nice to halves or the color but you can definitely check out my website to get a better understanding of what I’m trying to do

```html
<!DOCTYPE html>
<html lang="en">
<head>
<meta charset="utf-8">
<title>Gilded Slatworks – Business Card</title>
<link rel="stylesheet" href="https://fonts.googleapis.com/css2?family=Libre+Baskerville:wght@400;700&family=Montserrat:wght@400;500&display=swap">
<style>
  :root {
    --stage: #2b2b2b;
    --card-black: #050505;
    --gold: #c9ad4e;
    --gold-light: #e0c76a;
    --ink-white: #f2f2f2;
    --sky-top: #5d8fd0;
    --sky-bottom: #9cc0e6;
    --house-navy: #2c3342;
    --lawn: #4f5e38;
  }
  * { box-sizing: border-box; margin: 0; padding: 0; }
  html, body { width: 1200px; height: 875px; overflow: hidden; }
  body {
    background: var(--stage);
    display: flex;
    align-items: center;
    justify-content: center;
    gap: 40px;
  }
  .card {
    width: 540px;
    height: 309px;
    border-radius: 16px;
    overflow: hidden;
    position: relative;
    box-shadow: 0 14px 40px rgba(0,0,0,.45);
  }
  .card--photo .photo {
    width: 100%;
    height: 100%;
    background: linear-gradient(180deg, var(--sky-top) 0%, var(--sky-bottom) 30%, var(--house-navy) 55%, #3d4030 80%, var(--lawn) 100%);
  }
  .card--info {
    background: var(--card-black);
    display: flex;
    align-items: center;
    padding: 0 34px 0 40px;
  }
  .brand {
    flex: 0 0 220px;
    display: flex;
    flex-direction: column;
    align-items: center;
    text-align: center;
    margin-top: 60px;
  }
  .brand__name {
    font-family: "Libre Baskerville", serif;
    font-weight: 400;
    font-size: 27px;
    line-height: 1.15;
    color: var(--gold);
  }
  .brand__tagline {
    margin-top: 10px;
    font-family: "Libre Baskerville", serif;
    font-weight: 700;
    font-size: 12px;
    color: var(--gold);
    word-spacing: 10px;
  }
  .divider {
    width: 1.5px;
    height: 170px;
    background: var(--ink-white);
    margin: 0 20px 0 28px;
  }
  .contact {
    font-family: "Montserrat", sans-serif;
    color: var(--ink-white);
    font-size: 12.5px;
    line-height: 1.35;
  }
  .contact__name {
    font-family: "Libre Baskerville", serif;
    font-weight: 700;
    font-size: 19px;
    color: var(--gold-light);
    margin-bottom: 2px;
  }
  .contact__title { margin-bottom: 4px; }
  .contact__service { margin-bottom: 12px; }
  .contact__line {
    display: flex;
    align-items: center;
    gap: 8px;
    margin-bottom: 4px;
  }
  .contact__line svg { width: 13px; height: 13px; flex: none; }
  .contact__note {
    margin-top: 6px;
    color: var(--gold);
    font-weight: 500;
  }
</style>
</head>
<body>
  <section class="card card--photo">
    <div class="photo" role="img" aria-label="Photograph of a two-storey home with a covered porch fitted with dark exterior shades, trees and garden in front"></div>
  </section>

  <section class="card card--info">
    <div class="brand">
      <div class="brand__name">Gilded<br>Slatworks</div>
      <div class="brand__tagline">Shutters Shades Blinds</div>
    </div>
    <div class="divider"></div>
    <div class="contact">
      <div class="contact__name">Daniel Trevick</div>
      <div class="contact__title">Owner</div>
      <div class="contact__service">Custom Interior &amp; Exterior<br>Window Treatments</div>
      <div class="contact__line">
        <svg viewBox="0 0 24 24" aria-hidden="true"><path fill="var(--ink-white)" d="M6.6 10.8a15.1 15.1 0 0 0 6.6 6.6l2.2-2.2a1 1 0 0 1 1-.25 11.4 11.4 0 0 0 3.6.57 1 1 0 0 1 1 1V20a1 1 0 0 1-1 1A17 17 0 0 1 3 4a1 1 0 0 1 1-1h3.5a1 1 0 0 1 1 1c0 1.25.2 2.45.57 3.6a1 1 0 0 1-.25 1z"/></svg>
        <span>919-555-0148</span>
      </div>
      <div class="contact__line">
        <svg viewBox="0 0 24 24" aria-hidden="true"><circle cx="12" cy="12" r="9" fill="none" stroke="var(--ink-white)" stroke-width="2"/><path d="M3 12h18M12 3c3 3 3 15 0 18M12 3c-3 3-3 15 0 18" fill="none" stroke="var(--ink-white)" stroke-width="1.6"/></svg>
        <span>GildedSlatworks.com</span>
      </div>
      <div class="contact__note">By Appointment</div>
    </div>
  </section>
</body>
</html>
```